New Business Card Design Project LORVANTI-Italy

we are LORVANTI-Italy
our company in the market for 3 years we are luxury cosmetic company and its about time for a facelift :)
i will like to have elegant luxurious and unique business card
that will give the person that get it a unique, luxurious and elegant impression
I'm VERY OPEN FOR NEW IDEAS , even duo i add a few files of things that i see on line and i like them

i add my logo as well
my website is LORVANTI.COM
(if you would like to see the main style that we have)

Target Market(s)

adult that have money :)

Industry/Entity Type

Business

Contact Information for Business Card

Name - Dario Lorvanti
Position - CEO and CO Founder
address - 4817 E Halvern
telephone - 555-384-1926
email - dario@lorvanti.com
fax - 555-384-1926
website - LORVANTI.COM

Colors
000000
959595
fbee3e
ffffff

Requirements
Must have
• big logo in GOLD color
• elegant look
• impressive
Nice to have
• not must but maybe classy pattern background
• not must but maybe emblem
• maybe clear plastic business card
Should not have
• colors
• images

```html
<!DOCTYPE html>
<html lang="en">
<head>
<meta charset="utf-8">
<title>LORVANTI Italy – Business Card</title>
<link rel="stylesheet" href="https://fonts.googleapis.com/css2?family=Cinzel:wght@400;500&family=Roboto:wght@300;400&display=swap">
<style>
  :root {
    --backdrop: #3a312b;
    --card-black: #0d0d0d;
    --card-edge: #1c1c1c;
    --gold: #d8b82f;
    --grey: #959595;
    --light: #d4d4d4;
  }
  * { margin: 0; padding: 0; box-sizing: border-box; }
  html, body { width: 1200px; height: 1200px; overflow: hidden; }
  body { background: var(--backdrop); position: relative; font-family: "Roboto", sans-serif; }

  .card {
    position: absolute;
    left: 215px;
    width: 771px;
    height: 438px;
    background: radial-gradient(ellipse at 40% 35%, #1a1a1a 0%, var(--card-black) 70%);
    box-shadow: 0 6px 18px rgba(0,0,0,0.55);
    overflow: hidden;
  }
  .card--front { top: 151px; }
  .card--back  { top: 633px; }

  .card__pattern {
    position: absolute; inset: 0;
    background: linear-gradient(135deg, #161616 0%, #0c0c0c 55%, #141414 100%);
  }

  .emblem {
    position: absolute;
    border: 3px solid var(--gold);
    border-radius: 50%;
  }
  .card--front .emblem { left: 140px; top: 94px; width: 128px; height: 128px; }
  .card--back .emblem  { left: 295px; top: 45px; width: 180px; height: 180px; }

  .brand {
    position: absolute;
    font-family: "Cinzel", serif;
    font-weight: 400;
    color: var(--gold);
    text-align: center;
    white-space: nowrap;
  }
  .card--front .brand__name { left: 44px; width: 320px; top: 262px; font-size: 50px; line-height: 56px; }
  .card--back  .brand__name { left: 135px; width: 500px; top: 256px; font-size: 76px; line-height: 86px; }

  .brand__rule { position: absolute; height: 3px; background: var(--gold); }
  .card--front .brand__rule { left: 64px; width: 280px; top: 313px; }
  .card--back  .brand__rule { left: 188px; width: 394px; top: 352px; }

  .card--front .brand__country { left: 44px; width: 320px; top: 325px; font-size: 21px; line-height: 26px; }
  .card--back  .brand__country { left: 135px; width: 500px; top: 368px; font-size: 29px; line-height: 36px; }

  .divider {
    position: absolute; left: 386px; top: 97px;
    width: 2px; height: 243px; background: var(--gold);
  }

  .person { position: absolute; left: 428px; top: 86px; }
  .person__name {
    font-family: "Cinzel", serif; font-weight: 500;
    font-size: 31px; letter-spacing: 2px; color: var(--gold); line-height: 38px;
  }
  .person__role { font-size: 18px; font-weight: 300; color: var(--grey); line-height: 24px; }

  .contact { position: absolute; left: 428px; top: 200px; list-style: none; }
  .contact li { font-size: 17px; font-weight: 400; color: var(--light); line-height: 31px; }
</style>
</head>
<body>

  <section class="card card--front" aria-label="Business card front">
    <div class="emblem"></div>
    <div class="brand brand__name">LORVANTI</div>
    <div class="brand__rule"></div>
    <div class="brand brand__country">ITALY</div>

    <div class="divider"></div>

    <div class="person">
      <div class="person__name">DARIO LORVANTI</div>
      <div class="person__role">CEO and CO Founder</div>
    </div>

    <ul class="contact">
      <li>Tel. 555-384-1926</li>
      <li>Fax. 555-384-1926</li>
      <li>dario@lorvanti.com</li>
      <li>www.lorvanti.com</li>
      <li>Address. 4817 E Halvern</li>
    </ul>
  </section>

  <section class="card card--back" aria-label="Business card back">
    <div class="card__pattern" role="img" aria-label="Subtle diagonal lattice pattern on black card stock"></div>
    <div class="emblem"></div>
    <div class="brand brand__name">LORVANTI</div>
    <div class="brand__rule"></div>
    <div class="brand brand__country">ITALY</div>
  </section>

</body>
</html>
```